Bespoke Builders Business Card Design

We need a business card for an established builder of high quality bespoke homes in Auckland and Northland. We build and renovate homes collaboratively facilitating effective communication between owners, builders, architects, suppliers and tradespeople. We have never built or renovated a home that leaks or has faults. We only use reliable materials. We have never been sued or had legal action taken against us. We are honest builders of bespoke homes not group mass produced homes. Our niche market is in character homes. We practice sustainability and have built a lot of coastal property. We have been in business for over thirty years . We would like to see natural colors of the environment sand,sea and maybe vegetation . The design should communicate quality, sustainability,fair pricing, open communication and the originality of bespoke building. And the fact that the builder is registered.

Industry/Entity Type

Business

Contact Information for Business Card

Rowan Tellick Builders
Ph. 021583917
18 Kestrel Rd Harwood Bay Auckland 0814
PO Box 927 Mangawhai 0583

```html
<!DOCTYPE html>
<html lang="en">
<head>
<meta charset="utf-8">
<title>Rowan Tellick Builders – Business Card</title>
<link rel="stylesheet" href="https://fonts.googleapis.com/css2?family=PT+Serif&family=Carlito&display=swap">
<style>
  :root {
    --page-bg: #e6e4df;
    --card-bg: #f7f7f5;
    --ink: #1c1c1c;
    --accent-blue: #3a3f9b;
    --rule: #3a3a3a;
    --card-shadow: rgba(0, 0, 0, 0.18);
  }
  * { box-sizing: border-box; margin: 0; padding: 0; }
  html, body {
    width: 1200px;
    height: 892px;
    overflow: hidden;
    background: var(--page-bg);
  }
  .canvas {
    width: 1200px;
    height: 892px;
    display: flex;
    flex-direction: column;
    align-items: center;
    justify-content: center;
    gap: 44px;
  }
  .card {
    position: relative;
    width: 640px;
    height: 366px;
    background: var(--card-bg);
    box-shadow: 0 6px 18px var(--card-shadow);
    overflow: hidden;
  }
  .card-front {
    display: flex;
    align-items: center;
    justify-content: center;
  }
  .front-name {
    font-family: "PT Serif", serif;
    font-size: 50px;
    font-weight: 400;
    color: var(--ink);
    letter-spacing: 0.5px;
  }
  .corner-accents {
    position: absolute;
    inset: 0;
    width: 100%;
    height: 100%;
  }
  .corner-accents polygon { fill: var(--accent-blue); }
  .card-back-content {
    position: absolute;
    inset: 0;
    display: flex;
    flex-direction: column;
    align-items: center;
    justify-content: center;
    padding-top: 6px;
  }
  .back-name {
    font-family: "PT Serif", serif;
    font-size: 38px;
    font-weight: 400;
    color: var(--ink);
    letter-spacing: 0.3px;
  }
  .name-rule {
    width: 410px;
    height: 1px;
    background: var(--rule);
    margin: 14px 0 26px;
  }
  .contact-list {
    list-style: none;
    text-align: center;
    font-family: "Carlito", sans-serif;
    font-size: 18px;
    line-height: 1.3;
    color: var(--ink);
  }
</style>
</head>
<body>
  <main class="canvas">
    <section class="card card-front" aria-label="Business card front">
      <h1 class="front-name">Rowan Tellick Builders</h1>
    </section>

    <section class="card card-back" aria-label="Business card back">
      <svg class="corner-accents" viewBox="0 0 640 366" preserveAspectRatio="none" aria-hidden="true">
        <polygon points="0,0 230,0 0,200"/>
        <polygon points="640,366 410,366 640,166"/>
      </svg>
      <div class="card-back-content">
        <h2 class="back-name">Rowan Tellick Builders</h2>
        <div class="name-rule"></div>
        <ul class="contact-list">
          <li class="contact-phone">021583917</li>
          <li class="contact-address">18 Kestrel Rd Harwood Bay Auckland 0814</li>
          <li class="contact-postal">PO Box 927 Mangawhai 0583</li>
        </ul>
      </div>
    </section>
  </main>
</body>
</html>
```